RW Holloway LLC Business Card - Civil Engineering & Consulting Firm

We need a Business Card that is elegant, and masculine.  It is our Professional Civil Engineering & Consulting Company located in San Antonio TX (Not s construction or builder firm- no gears & no tool images please). We provide civil engineering services including  commercial site plans, grading and drainage plans, utility plans, hydraulics and hydrology, land planning, utility coordination, and other general civil engineering services related to commercial and residential development.
We have 2 existing Logos. We would like to convey reliability, strength, trustworthiness and attention to detail.  Blues and orange tones as per logo We are OK with the use of a darker blue in the mix.  We have 2 logo versions - Full Company Name Logo to go on the back of card, & Small Icon Logo for the front w/ personal Info.

Target Market(s)
Architects, Real Estate Developers, Other Strctural Engineers, Surveyers, General Contractors
Industry/Entity Type
Professional Civil Engineering
Contact Information for Business Card
Name, Position, Address, Cell & Office #, email, and company website
Font styles to use
Other font styles liked:
- Avian
Requirements
Should not have
- No Tools, No Gears, no Cranes, or Construction Equipment.

```html
<!DOCTYPE html>
<html lang="en">
<head>
<meta charset="utf-8">
<title>RW Holloway LLC – Business Card</title>
<link rel="stylesheet" href="https://fonts.googleapis.com/css2?family=Josefin+Sans:wght@300;400&family=Arimo:wght@400&display=swap">
<style>
  :root {
    --canvas: #e4e4e4;
    --card-dark: #262626;
    --card-light: #f6f6f6;
    --brand-blue: #6aa6dc;
    --brand-orange: #f0902a;
    --ink: #1e1e1e;
    --shadow: rgba(0, 0, 0, 0.18);
  }
  * { box-sizing: border-box; margin: 0; padding: 0; }
  html, body {
    width: 1200px;
    height: 930px;
    overflow: hidden;
    background: var(--canvas);
  }
  .canvas {
    position: relative;
    width: 1200px;
    height: 930px;
  }
  .card {
    position: absolute;
    width: 560px;
    height: 320px;
    box-shadow: 0 10px 24px var(--shadow);
    overflow: hidden;
  }

  /* Back of card: full company name */
  .card-back {
    left: 590px;
    top: 140px;
    background: var(--card-dark);
    display: flex;
    align-items: center;
    justify-content: center;
  }
  .company-name {
    font-family: "Josefin Sans", sans-serif;
    font-weight: 300;
    font-size: 40px;
    letter-spacing: 6px;
    text-transform: uppercase;
    color: var(--brand-blue);
    display: flex;
    align-items: center;
    gap: 16px;
  }
  .company-mark {
    width: 18px;
    height: 18px;
    background: var(--brand-orange);
    flex: none;
  }

  /* Front of card: personal details */
  .card-front {
    left: 50px;
    top: 470px;
    background: var(--card-light);
    display: flex;
  }
  .front-brand {
    width: 210px;
    height: 100%;
    background: var(--card-dark);
    display: flex;
    align-items: center;
    justify-content: center;
    padding: 20px;
  }
  .front-brand .company-name {
    font-size: 19px;
    letter-spacing: 2px;
    gap: 10px;
  }
  .front-brand .company-mark {
    width: 12px;
    height: 12px;
  }
  .contact {
    flex: 1;
    padding: 58px 0 0 44px;
    font-family: "Arimo", sans-serif;
    color: var(--ink);
  }
  .person-name {
    font-family: "Josefin Sans", sans-serif;
    font-weight: 400;
    font-size: 24px;
    letter-spacing: 1.5px;
    text-transform: uppercase;
    color: var(--brand-blue);
  }
  .person-name .surname { color: var(--brand-orange); }
  .person-role {
    font-size: 15px;
    margin-top: 4px;
  }
  .contact-list {
    list-style: none;
    margin-top: 18px;
    font-size: 15px;
    line-height: 22px;
  }
  .contact-list li {
    display: flex;
    align-items: center;
    gap: 8px;
  }
  .contact-list svg {
    width: 13px;
    height: 13px;
    flex: none;
    fill: var(--brand-blue);
  }
  .web-accent { color: var(--brand-orange); }
  .address {
    margin-top: 20px;
    font-size: 15px;
    line-height: 20px;
  }
</style>
</head>
<body>
<main class="canvas">

  <section class="card card-back" aria-label="Business card back">
    <div class="company-name"><span class="company-mark"></span>RW Holloway LLC</div>
  </section>

  <section class="card card-front" aria-label="Business card front">
    <div class="front-brand">
      <div class="company-name"><span class="company-mark"></span>RW Holloway LLC</div>
    </div>
    <div class="contact">
      <h1 class="person-name">Daniel <span class="surname">Reyes</span></h1>
      <p class="person-role">Managing Director</p>
      <ul class="contact-list">
        <li>
          <svg viewBox="0 0 16 16" aria-hidden="true"><path d="M3.6 1.2l2.3 2.4-1.3 1.8c.9 2 2.5 3.6 4.4 4.5l1.8-1.3 2.4 2.3-1.3 2.5C7 13.2 2.8 9 1.2 4.3z"/></svg>
          210-555 014 732
        </li>
        <li>
          <svg viewBox="0 0 16 16" aria-hidden="true"><path d="M1 3h14v10H1zm1.5 1.3L8 8.6l5.5-4.3z"/></svg>
          office@holloway-civil.com
        </li>
        <li>
          <svg viewBox="0 0 16 16" aria-hidden="true"><circle cx="8" cy="8" r="7"/></svg>
          www.<span class="web-accent">holloway-civil</span>.com
        </li>
      </ul>
      <p class="address">118, Alamo Ridge Drive<br>78205, San Antonio TX</p>
    </div>
  </section>

</main>
</body>
</html>
```